Company web site

Looking for a full responsive(mobile friendly) wordpress implementation

Some material is in the website -- brelvanto.wordpress.com

But looking for a template more consistent with the logo design, and more future looking.

Target Market(s)

Enterprise Clients

Industry/Entity Type

It Company

Font styles to use
Sans Serif

Colors
33a6d7
0255a3
0455a3
cfdeed
85abd2
3176b5

Requirements
Must have
• about, contact information, partner page, success stories, customer testimonials. links to social presence.
• pricing information

```html
<!DOCTYPE html>
<html lang="en">
<head>
<meta charset="utf-8">
<title>Brelvanto</title>
<link rel="stylesheet" href="https://fonts.googleapis.com/css2?family=Lato:ital,wght@0,400;0,700;1,400&family=Oswald:wght@300;400&family=Play:wght@400;700&display=swap">
<style>
:root{
  --blue:#2a9fd9;
  --blue-dark:#0255a3;
  --navy:#1a1f2b;
  --ink:#3a3a3a;
  --grey:#5b5b5b;
  --grey-arc:#606265;
  --light:#eeeeee;
  --line:#cfcfcf;
  --white:#ffffff;
}
*{margin:0;padding:0;box-sizing:border-box}
html,body{width:1200px;height:3072px;overflow:hidden}
body{font-family:"Lato",sans-serif;color:var(--ink);background:var(--white);position:relative}
.abs{position:absolute}
.heading{font-family:"Play",sans-serif;font-weight:400;color:var(--ink)}
.heading span{color:var(--blue)}
.section-title{position:absolute;left:0;width:1200px;text-align:center;font-size:36px}
.title-rule{position:absolute;height:2px;background:var(--line)}

/* header */
.site-header{position:absolute;top:0;left:0;width:1200px;height:121px;background:var(--white)}
.brand{position:absolute;left:98px;top:52px;display:flex;align-items:center;gap:10px;font-family:"Play",sans-serif;font-weight:700;font-size:30px;color:var(--blue)}
.brand i{display:block;width:22px;height:22px;border-radius:50%;background:var(--blue)}
.contact-chip{position:absolute;top:14px;display:flex;align-items:center;gap:11px;font-size:16px;color:var(--grey)}
.contact-chip b{display:flex;align-items:center;justify-content:center;width:33px;height:33px;background:var(--blue);border-radius:3px}
.main-nav{position:absolute;top:90px;left:410px;display:flex;gap:0;font-family:"Play",sans-serif;font-size:16px;color:var(--ink)}
.main-nav a{text-decoration:none;color:inherit;margin-right:38px;position:relative;padding-bottom:6px}
.main-nav a.active{color:var(--blue)}
.main-nav a.active::after{content:"";position:absolute;left:0;right:0;bottom:-2px;height:3px;background:var(--blue)}

/* hero */
.hero{position:absolute;top:121px;left:0;width:1200px;height:530px;background:radial-gradient(circle at 310px 230px,#4fc4ff 0,#1a6fb5 90px,#0b3563 200px,#06142a 380px,#030a16 700px)}
.hero-title{position:absolute;right:98px;top:275px;text-align:right;font-family:"Oswald",sans-serif;font-weight:300;font-size:38px;line-height:46px;color:var(--white)}
.hero-dots{position:absolute;left:1036px;top:415px;display:flex;gap:6px}
.hero-dots i{width:12px;height:12px;border-radius:50%;background:var(--white)}
.hero-dots i.on{background:var(--blue);border:2px solid var(--white)}

/* welcome */
.welcome{position:absolute;top:651px;left:0;width:1200px;height:414px;background:var(--white)}
.welcome h1{position:absolute;left:100px;top:46px;font-size:36px}
.welcome .rule{position:absolute;left:100px;top:103px;width:553px;height:1px;background:var(--line)}
.welcome p{position:absolute;left:100px;width:555px;font-size:15px;line-height:24px;color:#2e2e2e}
.btn{position:absolute;left:100px;top:326px;width:127px;height:39px;background:var(--blue);color:var(--white);font-size:15px;font-weight:700;display:flex;align-items:center;justify-content:center}
.video{position:absolute;left:698px;top:54px;width:402px;height:300px;border:3px solid #222;background:linear-gradient(135deg,#c9c3b8,#8a8e95 55%,#4a4e58);box-shadow:0 4px 10px rgba(0,0,0,.35)}
.video-bar{position:absolute;left:0;right:0;bottom:0;height:34px;background:#1b1b1b;color:#ddd;font-size:11px}
.video-bar .track{position:absolute;left:0;right:0;top:0;height:4px;background:#555}
.video-bar .track i{display:block;width:38px;height:4px;background:#d22}

/* how it works */
.how{position:absolute;top:1065px;left:0;width:1200px;height:532px;background:var(--light)}
.step{position:absolute;top:148px;width:200px;margin-left:-100px;text-align:center}
.step h3{font-family:"Play",sans-serif;font-size:20px;font-weight:700;color:var(--ink);margin-top:12px;line-height:28px}
.step ul{list-style:none;font-size:14px;line-height:26.6px;color:#222;margin-top:4px}
.step ul li::before{content:"• "}
.step ul li.more::before{content:""}
.op{position:absolute;top:195px;font-size:34px;font-weight:700;color:var(--blue);font-family:"Play",sans-serif}

/* lifecycle */
.lifecycle{position:absolute;top:1597px;left:0;width:1200px;height:471px;background:var(--white)}
.stage-label{position:absolute;width:160px;margin-left:-80px;text-align:center;font-size:16px;color:#222}
.stage-dot{position:absolute;width:24px;height:24px;margin-left:-12px;border-radius:50%;display:flex;align-items:center;justify-content:center}

/* testimonials */
.testimonials{position:absolute;top:2068px;left:0;width:1200px;height:410px;background:var(--light)}
.quote{position:absolute;left:160px;top:124px;width:880px;text-align:center;font-size:13.5px;font-style:italic;line-height:27px;color:#333}
.avatar{position:absolute;border-radius:50%;background:radial-gradient(circle at 50% 40%,#e9c9b0,#b68a6e 60%,#6b5448)}
.client-name{position:absolute;left:0;width:1200px;top:358px;text-align:center;font-size:14px;font-weight:700;color:#444}

/* partners */
.partners{position:absolute;top:2478px;left:0;width:1200px;height:246px;background:var(--white)}
.partner{position:absolute;top:119px;width:143px;height:74px;border:1px solid #d5d5d5;display:flex;align-items:center;justify-content:center}
.partner i{display:block;width:92px;height:22px;border-radius:4px;background:#cfcfcf}
.slide-arrow{position:absolute;top:137px;width:38px;height:38px;border-radius:50%;background:#e6e6e6;display:flex;align-items:center;justify-content:center}

/* footer */
.site-footer{position:absolute;top:2724px;left:0;width:1200px;height:307px;background:var(--navy);color:#e6e6e6}
.site-footer h4{position:absolute;top:40px;font-family:"Play",sans-serif;font-weight:700;font-size:18px;color:var(--white)}
.site-footer h4 span{color:var(--blue)}
.foot-rule{position:absolute;top:74px;height:1px;background:#3a4050}
.quick-links{position:absolute;left:100px;top:92px;list-style:none;font-size:11.5px;line-height:31.5px}
.quick-links li::before{content:"• "}
.quick-links li.on{color:var(--blue)}
.address{position:absolute;left:328px;top:92px;font-size:12.5px;line-height:18px}
.address b{font-size:14px;font-weight:400}
.foot-contact{position:absolute;left:328px;display:flex;align-items:center;gap:14px;font-size:12.5px}
.map{position:absolute;left:569px;top:88px;width:297px;height:172px;background:linear-gradient(140deg,#e8e6e1,#d8d6d0 60%,#cfd8e2);border:2px solid #333}
.foot-brand{position:absolute;left:948px;top:150px;display:flex;align-items:center;gap:8px;font-family:"Play",sans-serif;font-weight:700;font-size:21px;color:#bfc4cc}
.foot-brand i{width:16px;height:16px;border-radius:50%;background:#bfc4cc;display:block}
.social{position:absolute;top:198px;width:29px;height:29px;border-radius:50%}
.copyright{position:absolute;top:3031px;left:0;width:1200px;height:41px;background:var(--blue);color:var(--white);font-size:13px;display:flex;align-items:center;justify-content:center}
</style>
</head>
<body>

<header class="site-header">
  <div class="brand"><i></i>Brelvanto</div>
  <div class="contact-chip" style="left:690px">
    <b><svg width="18" height="18" viewBox="0 0 24 24"><path d="M6.6 10.8a15 15 0 0 0 6.6 6.6l2.2-2.2c.3-.3.7-.4 1-.2 1.1.4 2.3.6 3.6.6.6 0 1 .4 1 1V20c0 .6-.4 1-1 1A17 17 0 0 1 3 4c0-.6.4-1 1-1h3.5c.6 0 1 .4 1 1 0 1.3.2 2.5.6 3.6.1.3 0 .7-.2 1z" fill="#fff"/></svg></b>
    +1-(555) 014-2750
  </div>
  <div class="contact-chip" style="left:909px;font-size:14px">
    <b><svg width="18" height="14" viewBox="0 0 20 14"><rect x="0" y="0" width="20" height="14" rx="1" fill="#fff"/><path d="M1 1l9 7 9-7" stroke="#2a9fd9" stroke-width="1.6" fill="none"/></svg></b>
    info@brelvanto.com
  </div>
  <nav class="main-nav">
    <a class="active">Home</a><a>About</a><a>Partner</a><a>Success Stories</a><a>Customer Testimonials</a><a style="margin-right:0">Contact</a>
  </nav>
</header>

<section class="hero">
  <div class="abs" role="img" aria-label="Open hand holding a glowing blue digital globe on a dark background" style="inset:0"></div>
  <h2 class="hero-title">Bridging Connected Devices<br>With Enterprise Solutions</h2>
  <div class="hero-dots"><i class="on"></i><i></i><i></i><i></i></div>
</section>

<section class="welcome">
  <h1 class="heading">Welcome To <span>Brel</span>vanto</h1>
  <div class="rule"></div>
  <p style="top:124px">Lorem ipsum dolor sit amet, consectetuer adipiscing elit, sed diam nonummy nibh euismod tincidunt ut laoreet dolore magna aliquam erat volutpat.</p>
  <p style="top:180px">Lorem ipsum dolor sit amet, consectetuer adipiscing elit, sed diam nonummy nibh euismod tincidunt ut laoreet dolore magna aliquam erat volutpat. Ut wisi enim ad minim veniam, quis nostrud exerci tation ullamcorper suscipit lobortis nisl ut aliquip ex ea commodo consequat. Duis autem vel eum iriure dolor in hendrerit in vulputate velit esse molestie consequat, vel illum dolore eu feugiat nulla facilisis at vero eros et accumsan et iusto.</p>
  <div class="btn">Learn More</div>
  <div class="video">
    <div class="abs" role="img" aria-label="Video still of a business team meeting around a table" style="inset:0 0 34px 0"></div>
    <div class="video-bar">
      <div class="track"><i></i></div>
      <svg class="abs" style="left:10px;top:12px" width="14" height="14" viewBox="0 0 14 14"><rect x="2" y="1" width="3.5" height="12" fill="#ddd"/><rect x="8.5" y="1" width="3.5" height="12" fill="#ddd"/></svg>
      <span class="abs" style="left:106px;top:12px">3:16 / 57:21</span>
      <svg class="abs" style="right:12px;top:11px" width="16" height="14" viewBox="0 0 16 14"><path d="M1 1h5M1 1v4M15 1h-5M15 1v4M1 13h5M1 13V9M15 13h-5M15 13V9" stroke="#ddd" stroke-width="2" fill="none"/></svg>
    </div>
  </div>
</section>

<section class="how">
  <h2 class="heading section-title" style="top:50px">How It <span>Works</span></h2>
  <div class="title-rule" style="left:467px;top:104px;width:266px"></div>

  <svg class="abs" style="left:0;top:140px" width="1200" height="120" viewBox="0 0 1200 120">
    <defs>
      <path id="cloud" d="M-44 40a22 22 0 0 1 2-44 34 34 0 0 1 64-12 26 26 0 0 1 34 28 20 20 0 0 1 4 28" fill="none" stroke="#a9d3ee" stroke-width="11" stroke-linecap="round"/>
    </defs>
    <g transform="translate(160,60)"><use href="#cloud"/><circle cx="18" cy="0" r="9" fill="#333"/><rect x="4" y="12" width="28" height="22" rx="6" fill="#333"/></g>
    <g transform="translate(452,60)"><use href="#cloud"/><g transform="rotate(-45 18 18)" fill="none" stroke="#333" stroke-width="6"><rect x="2" y="10" width="20" height="14" rx="7"/><rect x="16" y="10" width="20" height="14" rx="7"/></g></g>
    <g transform="translate(744,60)"><use href="#cloud"/><circle cx="8" cy="24" r="9" fill="none" stroke="#333" stroke-width="6" stroke-dasharray="4 3"/><circle cx="28" cy="6" r="8" fill="none" stroke="#333" stroke-width="5" stroke-dasharray="3 3"/></g>
    <g transform="translate(1004,60)"><use href="#cloud"/><g stroke="#333" stroke-width="3"><line x1="18" y1="16" x2="2" y2="0"/><line x1="18" y1="16" x2="36" y2="0"/><line x1="18" y1="16" x2="2" y2="34"/><line x1="18" y1="16" x2="36" y2="34"/></g><g fill="#333"><circle cx="18" cy="16" r="6"/><circle cx="2" cy="0" r="5"/><circle cx="36" cy="0" r="5"/><circle cx="2" cy="34" r="5"/><circle cx="36" cy="34" r="5"/></g></g>
  </svg>
  <span class="op" style="left:299px">+</span>
  <span class="op" style="left:590px">+</span>
  <span class="op" style="left:880px">=</span>

  <div class="step" style="left:164px;top:288px"><h3>Learn</h3><ul><li>Properties</li><li>Actions</li><li>Events</li></ul></div>
  <div class="step" style="left:455px;top:288px"><h3>Connect</h3><ul><li>Skyline IoT</li><li>Cobalt IoT</li><li>Linkra</li><li>Varenta</li><li>Omnithing</li><li class="more">... and others</li></ul></div>
  <div class="step" style="left:748px;top:288px"><h3>Integrate</h3><ul><li>CRM systems</li><li>HelpNest</li><li>Social login</li><li>Triggerly</li><li>Billing</li><li class="more">... and many others</li></ul></div>
  <div class="step" style="left:1008px;top:288px"><h3>Connected<br>Product</h3></div>
</section>

<section class="lifecycle">
  <h2 class="heading section-title" style="top:58px">End-to-end Product <span>Lifecycle Management</span></h2>
  <div class="title-rule" style="left:182px;top:110px;width:836px"></div>

  <div class="stage-label" style="left:184px;top:130px">Manufacture</div>
  <div class="stage-label" style="left:463px;top:130px">Provision</div>
  <div class="stage-label" style="left:737px;top:130px">Support</div>
  <div class="stage-label" style="left:1016px;top:130px">Maintain</div>
  <div class="stage-dot" style="left:184px;top:164px;background:var(--blue)"><svg width="10" height="10" viewBox="0 0 10 10"><path d="M3 1l4 4-4 4" stroke="#fff" stroke-width="2" fill="none"/></svg></div>
  <div class="stage-dot" style="left:463px;top:164px;background:var(--blue)"><svg width="10" height="10" viewBox="0 0 10 10"><path d="M3 1l4 4-4 4" stroke="#fff" stroke-width="2" fill="none"/></svg></div>
  <div class="stage-dot" style="left:737px;top:164px;background:var(--blue)"><svg width="10" height="10" viewBox="0 0 10 10"><path d="M3 1l4 4-4 4" stroke="#fff" stroke-width="2" fill="none"/></svg></div>
  <div class="stage-dot" style="left:1016px;top:164px;background:var(--blue)"><svg width="10" height="10" viewBox="0 0 10 10"><path d="M3 1l4 4-4 4" stroke="#fff" stroke-width="2" fill="none"/></svg></div>

  <svg class="abs" style="left:0;top:180px" width="1200" height="200" viewBox="0 0 1200 200">
    <g fill="none" stroke-width="30">
      <path d="M100 99 A84 84 0 0 0 184 183" stroke="#2a9fd9"/>
      <path d="M184 99 A72 72 0 0 1 328 99" stroke="#606265"/>
      <path d="M328 99 A67.5 67.5 0 0 0 463 99" stroke="#2a9fd9"/>
      <path d="M463 99 A68.5 68.5 0 0 1 600 99" stroke="#606265"/>
      <path d="M600 99 A68.5 68.5 0 0 0 737 99" stroke="#2a9fd9"/>
      <path d="M737 99 A70 70 0 0 1 877 99" stroke="#606265"/>
      <path d="M877 99 A69.5 69.5 0 0 0 1016 99" stroke="#2a9fd9"/>
      <path d="M1016 183 A84 84 0 0 0 1100 99" stroke="#2a9fd9"/>
    </g>
    <g fill="#fff" stroke="#d9d9d9" stroke-width="3">
      <circle cx="184" cy="99" r="54"/><circle cx="328" cy="99" r="54"/><circle cx="463" cy="99" r="54"/><circle cx="600" cy="99" r="54"/><circle cx="737" cy="99" r="54"/><circle cx="877" cy="99" r="54"/><circle cx="1016" cy="99" r="54"/>
    </g>
    <g fill="#4a4a4a">
      <circle cx="176" cy="104" r="13" fill="none" stroke="#4a4a4a" stroke-width="7" stroke-dasharray="5 4"/><circle cx="196" cy="86" r="9" fill="none" stroke="#4a4a4a" stroke-width="5" stroke-dasharray="4 3"/>
      <rect x="316" y="78" width="24" height="18" rx="2"/><path d="M300 112h22l10 6h18" stroke="#4a4a4a" stroke-width="4" fill="none"/>
      <path d="M444 108a14 14 0 0 1 4-26 18 18 0 0 1 32 6 11 11 0 0 1 0 20z" fill="none" stroke="#4a4a4a" stroke-width="4"/><path d="M458 92v16l12-8z"/>
      <rect x="580" y="88" width="40" height="24" rx="4" fill="none" stroke="#4a4a4a" stroke-width="4"/><rect x="588" y="96" width="18" height="4"/><rect x="588" y="103" width="12" height="4"/>
      <circle cx="737" cy="90" r="13"/><path d="M714 122a23 18 0 0 1 46 0z"/><path d="M720 92a17 17 0 0 1 34 0" fill="none" stroke="#4a4a4a" stroke-width="4"/>
      <circle cx="872" cy="96" r="10" fill="none" stroke="#4a4a4a" stroke-width="4"/><path d="M856 116l14-6 10 4 18-16" stroke="#4a4a4a" stroke-width="4" fill="none"/><path d="M892 92l8 0 0 8z"/>
      <rect x="1000" y="78" width="28" height="36" rx="3" fill="none" stroke="#4a4a4a" stroke-width="4"/><path d="M1006 90l3 3 5-5M1006 102l3 3 5-5" stroke="#4a4a4a" stroke-width="2.5" fill="none"/><circle cx="1030" cy="112" r="11"/><path d="M1030 106v12M1024 112h12" stroke="#fff" stroke-width="3"/>
    </g>
  </svg>

  <div class="stage-label" style="left:322px;top:364px">Sell</div>
  <div class="stage-label" style="left:600px;top:364px">Use</div>
  <div class="stage-label" style="left:877px;top:364px">Monetize</div>
  <div class="stage-dot" style="left:322px;top:398px;background:#4a4a4a"><svg width="10" height="10" viewBox="0 0 10 10"><path d="M3 1l4 4-4 4" stroke="#fff" stroke-width="2" fill="none"/></svg></div>
  <div class="stage-dot" style="left:600px;top:398px;background:#4a4a4a"><svg width="10" height="10" viewBox="0 0 10 10"><path d="M3 1l4 4-4 4" stroke="#fff" stroke-width="2" fill="none"/></svg></div>
  <div class="stage-dot" style="left:877px;top:398px;background:#4a4a4a"><svg width="10" height="10" viewBox="0 0 10 10"><path d="M3 1l4 4-4 4" stroke="#fff" stroke-width="2" fill="none"/></svg></div>
</section>

<section class="testimonials">
  <h2 class="heading section-title" style="top:36px">Client <span>Testimonials</span></h2>
  <div class="title-rule" style="left:438px;top:90px;width:324px"></div>
  <p class="quote">“ Lorem ipsum dolor sit amet, consectetuer adipiscing elit, sed diam nonummy nibh euismod tincidunt ut laoreet dolore magna aliquam erat volutpat. Lorem ipsum dolor sit amet, consectetuer adipiscing elit, seiam nonummy nibh euismod tincidunt ut laoreet dolore magna aliquam volutpat sed diam nonummy nibh euismod. ”</p>
  <svg class="abs" style="left:336px;top:206px" width="528" height="16" viewBox="0 0 528 16"><line x1="0" y1="2" x2="528" y2="2" stroke="#bdbdbd" stroke-width="2"/><path d="M256 2h16l-8 9z" fill="#8a8a8a"/></svg>
  <svg class="abs" style="left:398px;top:272px" width="24" height="40" viewBox="0 0 24 40"><path d="M20 2L4 20l16 18" stroke="#cfcfcf" stroke-width="4" fill="none"/></svg>
  <svg class="abs" style="left:778px;top:272px" width="24" height="40" viewBox="0 0 24 40"><path d="M4 2l16 18L4 38" stroke="#cfcfcf" stroke-width="4" fill="none"/></svg>
  <div class="avatar" role="img" aria-label="Portrait of a client" style="left:454px;top:253px;width:80px;height:80px;border:3px solid #bbb"></div>
  <div class="avatar" role="img" aria-label="Portrait of the featured client" style="left:553px;top:247px;width:94px;height:94px;border:4px solid var(--blue)"></div>
  <div class="avatar" role="img" aria-label="Portrait of a client" style="left:664px;top:253px;width:80px;height:80px;border:3px solid #bbb"></div>
  <div class="client-name">Miss. Lora Venhart</div>
</section>

<section class="partners">
  <h2 class="heading section-title" style="top:28px">Our <span>Partners</span></h2>
  <div class="title-rule" style="left:450px;top:80px;width:300px"></div>
  <div class="slide-arrow" style="left:36px"><svg width="12" height="16" viewBox="0 0 12 16"><path d="M9 2L3 8l6 6" stroke="#222" stroke-width="2.5" fill="none"/></svg></div>
  <div class="partner" style="left:98px"><i></i></div>
  <div class="partner" style="left:270px"><i></i></div>
  <div class="partner" style="left:442px"><i></i></div>
  <div class="partner" style="left:614px"><i></i></div>
  <div class="partner" style="left:786px"><i></i></div>
  <div class="partner" style="left:958px"><i></i></div>
  <div class="slide-arrow" style="left:1126px"><svg width="12" height="16" viewBox="0 0 12 16"><path d="M3 2l6 6-6 6" stroke="#222" stroke-width="2.5" fill="none"/></svg></div>
</section>

<footer class="site-footer">
  <h4 style="left:100px">Quick <span>Links</span></h4>
  <div class="foot-rule" style="left:100px;width:140px"></div>
  <ul class="quick-links">
    <li class="on">Home</li><li>About</li><li>Partner</li><li>Success Stories</li><li>Customer Testimonials</li><li>Contact</li>
  </ul>

  <h4 style="left:328px">Contact <span>Details</span></h4>
  <div class="foot-rule" style="left:328px;width:160px"></div>
  <div class="address"><b>Brelvanto</b><br>418 Harlow Ave<br>Fairmont, CA 95110</div>
  <div class="foot-contact" style="top:180px"><svg width="14" height="14" viewBox="0 0 24 24"><path d="M6.6 10.8a15 15 0 0 0 6.6 6.6l2.2-2.2c.3-.3.7-.4 1-.2 1.1.4 2.3.6 3.6.6.6 0 1 .4 1 1V20c0 .6-.4 1-1 1A17 17 0 0 1 3 4c0-.6.4-1 1-1h3.5c.6 0 1 .4 1 1 0 1.3.2 2.5.6 3.6.1.3 0 .7-.2 1z" fill="#ccc"/></svg>+1-(555) 014-2750</div>
  <div class="foot-contact" style="top:216px"><svg width="14" height="14" viewBox="0 0 14 14"><rect x="3" y="0" width="8" height="4" fill="#ccc"/><rect x="0" y="4" width="14" height="6" rx="1" fill="#ccc"/><rect x="3" y="9" width="8" height="5" fill="#ccc"/></svg>+1-(555) 014-2750</div>
  <div class="foot-contact" style="top:252px"><svg width="14" height="10" viewBox="0 0 20 14"><rect width="20" height="14" rx="1" fill="#ccc"/><path d="M1 1l9 7 9-7" stroke="#1a1f2b" stroke-width="1.6" fill="none"/></svg>info@brelvanto.com</div>

  <h4 style="left:569px">Location <span>Map</span></h4>
  <div class="foot-rule" style="left:569px;width:297px"></div>
  <div class="map" role="img" aria-label="Street map showing the office location">
    <svg class="abs" style="left:100px;top:50px" width="22" height="32" viewBox="0 0 22 32"><path d="M11 31C4 20 1 15 1 10a10 10 0 0 1 20 0c0 5-3 10-10 21z" fill="#d93a2b"/><circle cx="11" cy="10" r="4" fill="#8e1e14"/></svg>
  </div>

  <div class="foot-brand"><i></i>Brelvanto</div>
  <div class="social" style="left:955px;background:#3b5b98"></div>
  <div class="social" style="left:991px;background:#33a6d7"></div>
  <div class="social" style="left:1028px;background:#0e76a8"></div>
  <div class="social" style="left:1065px;background:#d34836"></div>
</footer>
<div class="copyright">Copyright © 2017 Brelvanto. All Rights Reserved.</div>

</body>
</html>
```